Company web site

Looking for a full responsive(mobile friendly) wordpress implementation

Some material is in the website -- brelvanto.wordpress.com

But looking for a template more consistent with the logo design, and more future looking.

Target Market(s)

Enterprise Clients

Industry/Entity Type

It Company

Font styles to use
Sans Serif

Colors
33a6d7
0255a3
0455a3
cfdeed
85abd2
3176b5

Requirements
Must have
• about, contact information, partner page, success stories, customer testimonials. links to social presence.
• pricing information

```html
<!DOCTYPE html>
<html lang="en">
<head>
<meta charset="utf-8">
<title>Brelvanto – Platform</title>
<link href="https://fonts.googleapis.com/css2?family=Exo+2:wght@400;500;600;700;800&family=Open+Sans:wght@400;600;700&display=swap" rel="stylesheet">
<style>
:root{
  --blue:#1e9fdc;
  --blue-dark:#0255a3;
  --topbar:#5a5a5a;
  --text:#555;
  --heading:#222;
  --crumb:#e2e2e2;
  --footer:#1b2838;
  --footer-line:#3a4a5e;
  --white:#fff;
}
*{margin:0;padding:0;box-sizing:border-box}
html,body{width:952px;height:1200px;overflow:hidden;background:#fff}
body{position:relative;font-family:"Open Sans",sans-serif;color:var(--text)}
.abs{position:absolute}

.topbar{left:0;top:0;width:952px;height:25px;background:var(--topbar)}
.topbar .call{left:63px;top:0;height:25px;display:flex;align-items:center;gap:6px;color:#eee;font-size:10px}
.topbar .call b{font-weight:700;color:#fff}
.topbar .social{right:64px;top:0;display:flex}
.topbar .social span{width:29px;height:25px;border-left:1px solid #777;display:flex;align-items:center;justify-content:center}
.topbar .social span:last-child{border-right:1px solid #777}
.topbar .social i{width:8px;height:8px;border-radius:50%;background:#eee}

.header{left:0;top:25px;width:952px;height:77px;background:#fff}
.brand{display:flex;align-items:center;gap:8px;font-family:"Exo 2",sans-serif;font-weight:700;color:var(--blue)}
.header .brand{left:63px;top:22px;font-size:22px}
.brand .dot{width:30px;height:30px;border-radius:50%;background:var(--blue)}
.nav{right:64px;top:0;height:77px;display:flex;align-items:center;font-family:"Exo 2",sans-serif;font-size:14px;color:var(--text)}
.nav a{color:inherit;text-decoration:none;padding:0 14px}
.nav .active{height:77px;width:88px;background:var(--blue);color:#fff;display:flex;flex-direction:column;align-items:center;justify-content:center;gap:4px;padding:0;margin:0 10px 0 6px;font-weight:500}

.hero{left:0;top:102px;width:952px;height:266px;background:linear-gradient(90deg,#050608 0%,#0a0d14 45%,#0f3658 62%,#2f7fbf 78%,#7fb4de 88%,#34577a 100%)}
.hero-title{left:63px;top:212px;font-family:"Exo 2",sans-serif;font-weight:600;font-size:26px;line-height:33px;color:#ddd}
.hero-title em{font-style:normal;color:var(--blue)}

.crumb{left:0;top:368px;width:952px;height:32px;background:var(--crumb);display:flex;align-items:center;padding-left:63px;gap:9px;font-size:11px;font-weight:700}
.crumb .here{color:var(--blue)}

.page-title{left:0;top:448px;width:952px;text-align:center;font-family:"Exo 2",sans-serif;font-weight:800;font-size:31px;color:var(--blue);letter-spacing:1px}
.divider{left:256px;top:493px;width:440px;height:18px}
.divider::before,.divider::after{content:"";position:absolute;top:9px;width:200px;height:1px;background:#ddd}
.divider::before{left:0}.divider::after{right:0}
.divider i{position:absolute;left:211px;top:0;width:18px;height:18px;border:2px solid #bbb;border-radius:50%}

.intro{left:63px;top:536px;width:420px;font-size:12px;line-height:16px}
.sub{left:63px;top:593px;font-size:13.5px;font-weight:700;color:var(--heading)}
.features{left:63px;top:619px;width:418px;list-style:none;font-size:12px;line-height:16px}
.features li{position:relative;padding-left:21px;margin-bottom:5px}
.features svg{position:absolute;left:1px;top:4px}
.visual{left:504px;top:539px;width:384px;height:284px;background:linear-gradient(180deg,#c7a0bd 0%,#9d8aad 30%,#4a5f80 60%,#1c2a44 100%)}
.btn{left:63px;top:836px;width:182px;height:31px;border:1px solid #555;border-radius:3px;display:flex;align-items:center;justify-content:center;font-family:"Exo 2",sans-serif;font-weight:600;font-size:13.5px;color:#333}

.footer{left:0;top:924px;width:952px;height:241px;background:var(--footer)}
.f-head{font-family:"Exo 2",sans-serif;font-weight:600;font-size:16.5px;color:#fff;padding-bottom:8px;border-bottom:1px solid var(--footer-line)}
.f-head em{font-style:normal;color:var(--blue)}
.links{left:63px;top:962px;width:105px}
.links ul{list-style:none;margin-top:17px;font-size:12px;color:#d8dde3}
.links li{height:22.5px;position:relative;padding-left:13px}
.links li::before{content:"";position:absolute;left:1px;top:7px;width:3px;height:3px;border-radius:50%;background:var(--blue)}
.links li.on{color:var(--blue);font-weight:600}
.contact{left:230px;top:962px;width:134px}
.contact-body{left:230px;top:1010px;width:200px;font-size:12px;color:#d8dde3;line-height:16px}
.contact-body .name{font-family:"Exo 2",sans-serif;font-size:13.5px;color:#fff;font-weight:700}
.contact-body .row{display:flex;align-items:center;gap:8px;margin-top:10px}
.location{left:465px;top:962px;width:120px}
.map{left:466px;top:1015px;width:190px;height:121px;border:2px solid #cfd4d9;background:linear-gradient(135deg,#e4e4e4,#d6d6d6)}
.f-brand{left:703px;top:1050px;width:185px;justify-content:center;font-size:25px}
.f-brand .dot{width:34px;height:34px}
.f-social{left:738px;top:1110px;width:114px;display:flex;justify-content:space-between}
.f-social i{width:9px;height:9px;border-radius:50%;background:#d8dde3}
.copyright{left:0;top:1165px;width:952px;height:35px;background:#27a3dc;display:flex;align-items:center;justify-content:center;color:#fff;font-size:12px}
.copyright b{font-weight:700;margin-left:3px}
</style>
</head>
<body>

<div class="abs topbar">
  <div class="abs call">
    <svg width="12" height="12" viewBox="0 0 24 24"><path fill="#eee" d="M6.6 10.8a15.2 15.2 0 0 0 6.6 6.6l2.2-2.2c.3-.3.7-.4 1-.2 1.1.4 2.3.6 3.6.6.6 0 1 .4 1 1V20c0 .6-.4 1-1 1A17 17 0 0 1 3 4c0-.6.4-1 1-1h3.5c.6 0 1 .4 1 1 0 1.3.2 2.5.6 3.6.1.3 0 .7-.2 1z"/></svg>
    <span>Call Us : <b>+123 456 7890</b></span>
  </div>
  <div class="abs social"><span><i></i></span><span><i></i></span><span><i></i></span><span><i></i></span></div>
</div>

<header class="abs header">
  <div class="abs brand"><span class="dot"></span>Brelvanto</div>
  <nav class="abs nav">
    <a href="#">Home</a>
    <a href="#" class="active">
      <svg width="22" height="18" viewBox="0 0 22 18"><path d="M11 1 21 6 11 11 1 6z" fill="#fff"/><path d="M1 9.5 11 14.5 21 9.5M1 13 11 18 21 13" fill="none" stroke="#fff" stroke-width="2"/></svg>
      Platform
    </a>
    <a href="#">Partners</a>
    <a href="#">Blog</a>
    <a href="#">About</a>
    <a href="#">Contact</a>
  </nav>
</header>

<div class="abs hero" role="img" aria-label="Hand holding a tablet with a glowing globe and floating network screens"></div>
<h1 class="abs hero-title">Bridging <em>Connected Devices</em><br>With <em>Enterprise Solutions</em></h1>

<div class="abs crumb">
  <span>HOME</span>
  <svg width="9" height="9" viewBox="0 0 10 10"><path d="M1 1l4 4-4 4M5 1l4 4-4 4" fill="none" stroke="#1e9fdc" stroke-width="1.5"/></svg>
  <span class="here">PLATFORM</span>
</div>

<h2 class="abs page-title">PLATFORM</h2>
<div class="abs divider"><i></i></div>

<p class="abs intro">Brelvanto, the customizable BV IoT platform for OEM's provides essential and complicated integrations to enable a connected product, be successfully launched.</p>
<h3 class="abs sub">Particular integrations include:</h3>
<ul class="abs features">
  <li><svg width="11" height="9" viewBox="0 0 11 9"><path d="M1 4.5 4 7.5 10 1.5" fill="none" stroke="#444" stroke-width="2"/></svg>Multrtennant Paas solution</li>
  <li><svg width="11" height="9" viewBox="0 0 11 9"><path d="M1 4.5 4 7.5 10 1.5" fill="none" stroke="#444" stroke-width="2"/></svg>Abstract device models and multi product support</li>
  <li><svg width="11" height="9" viewBox="0 0 11 9"><path d="M1 4.5 4 7.5 10 1.5" fill="none" stroke="#444" stroke-width="2"/></svg>Da, integration from loT Connected device clouds, such as Nimbra Cloud 10T, Arvalent, Thingora and gibers</li>
  <li><svg width="11" height="9" viewBox="0 0 11 9"><path d="M1 4.5 4 7.5 10 1.5" fill="none" stroke="#444" stroke-width="2"/></svg>Mobile Application Infrastructure (SDK) to support rap, brand. mobile Applicator development, Including in-app notIcatons</li>
  <li><svg width="11" height="9" viewBox="0 0 11 9"><path d="M1 4.5 4 7.5 10 1.5" fill="none" stroke="#444" stroke-width="2"/></svg>Business operations Integration with systems such as EDP, CRM, Support,ffing Systems, and other°. ne systems</li>
  <li><svg width="11" height="9" viewBox="0 0 11 9"><path d="M1 4.5 4 7.5 10 1.5" fill="none" stroke="#444" stroke-width="2"/></svg>REST APIrt towards other OEM integrations</li>
  <li><svg width="11" height="9" viewBox="0 0 11 9"><path d="M1 4.5 4 7.5 10 1.5" fill="none" stroke="#444" stroke-width="2"/></svg>Advanced toTService integration with Trigly , Vocaro Hub, and others.</li>
</ul>
<div class="abs visual" role="img" aria-label="City skyline at dusk overlaid with a network of connected device icons"></div>
<a class="abs btn">Download Our Brochure</a>

<footer class="abs footer"></footer>
<div class="abs links">
  <h4 class="f-head">Quick <em>Links</em></h4>
  <ul>
    <li class="on">Home</li><li>Platform</li><li>Partners</li><li>Blog</li><li>About</li><li>Contact</li>
  </ul>
</div>
<div class="abs contact"><h4 class="f-head">Contact <em>Details</em></h4></div>
<div class="abs contact-body">
  <div class="name">Brelvanto</div>
  <div>123, Lorem ipsum dolor sit amet, euismod - 123 456</div>
  <div class="row" style="margin-top:12px"><svg width="10" height="10" viewBox="0 0 24 24"><path fill="#1e9fdc" d="M6.6 10.8a15.2 15.2 0 0 0 6.6 6.6l2.2-2.2c.3-.3.7-.4 1-.2 1.1.4 2.3.6 3.6.6.6 0 1 .4 1 1V20c0 .6-.4 1-1 1A17 17 0 0 1 3 4c0-.6.4-1 1-1h3.5c.6 0 1 .4 1 1 0 1.3.2 2.5.6 3.6.1.3 0 .7-.2 1z"/></svg>123 456 7890</div>
  <div class="row"><svg width="10" height="10" viewBox="0 0 10 10"><rect x="2.5" y="0.5" width="5" height="3" fill="none" stroke="#1e9fdc"/><rect x="0" y="3.5" width="10" height="4" fill="#1e9fdc"/><rect x="2.5" y="6" width="5" height="3.5" fill="#fff" stroke="#1e9fdc"/></svg>123 456 7890</div>
  <div class="row"><svg width="11" height="8" viewBox="0 0 11 8"><rect width="11" height="8" fill="#1e9fdc"/><path d="M0 0 5.5 4.5 11 0" fill="none" stroke="#1b2838"/></svg>info@brelvanto.com</div>
</div>
<div class="abs location"><h4 class="f-head">Location <em>Map</em></h4></div>
<div class="abs map" role="img" aria-label="Street map with a pin at 418 Harlow Avenue"></div>
<div class="abs brand f-brand"><span class="dot"></span>Brelvanto</div>
<div class="abs f-social"><i></i><i></i><i></i><i></i></div>

<div class="abs copyright">Copyright © 2017 <b>Brelvanto</b>. All Right Reserved.</div>

</body>
</html>
```